Vantoq Business Card Project showing the logo and a marbo image on the rear

Design a whacky but professional business card, the logo is for the front and the Marbo image is for the rear. Happy to consider other open source Marbo Images if the designer wants to select one from the web. Vantoq is a competitor to OMB.com.au and Pellory.com.au and is based around every property in Australia

Target Market(s)

Business

Contact Information for Business Card

Name, Title, Email, Web, Phone Number

Font styles to use
Other font styles liked:
• avenir

Requirements
Must have
• Image on Back logo on front
Nice to have
• Happy to consider other images on rear, preftably Colin Marbo. Image supplied I own, we can use open source other Marbo Images

```html
<!DOCTYPE html>
<html lang="en">
<head>
<meta charset="utf-8">
<title>Vantoq Business Card</title>
<link href="https://fonts.googleapis.com/css2?family=Nunito+Sans:wght@400;600;800&display=swap" rel="stylesheet">
<style>
  :root {
    --page-bg: #2b2b2b;
    --card-white: #ffffff;
    --brand-orange: #f78c0c;
    --ink: #111111;
    --divider: #8a8a8a;
    --paper-white: #ffffff;
  }
  * { margin: 0; padding: 0; box-sizing: border-box; }
  html, body { width: 1200px; height: 1040px; overflow: hidden; }
  body {
    background: var(--page-bg);
    font-family: "Nunito Sans", "Avenir", sans-serif;
    display: flex;
    flex-direction: column;
    align-items: center;
    justify-content: center;
    gap: 56px;
  }
  .card {
    width: 760px;
    height: 434px;
    position: relative;
    overflow: hidden;
  }
  .card--back { border-radius: 70px 0 70px 0; }
  .card--front {
    background: var(--card-white);
    border-radius: 0 70px 0 70px;
  }
  .card__artwork {
    position: absolute;
    inset: 0;
    background:
      linear-gradient(180deg, rgba(10,14,30,0.35) 0%, rgba(10,10,15,0.6) 100%),
      linear-gradient(90deg, #3a4f6e 0%, #6b3b2e 22%, #5a5a1e 42%, #2d5a3a 55%, #7a4a16 70%, #6a2c36 84%, #245a66 100%);
  }
  .brand {
    position: absolute;
    left: 0; right: 0;
    display: flex;
    justify-content: center;
    align-items: center;
    gap: 22px;
    font-weight: 800;
    letter-spacing: 1px;
    line-height: 1;
  }
  .brand__mark {
    width: 60px;
    height: 60px;
    background: var(--brand-orange);
  }
  .card--back .brand {
    top: 170px;
    font-size: 92px;
    color: var(--paper-white);
  }
  .card--front .brand {
    top: 76px;
    font-size: 100px;
    color: var(--ink);
  }
  .card--front .brand__mark { width: 72px; height: 72px; }
  .contact-block {
    position: absolute;
    left: 0; right: 0; top: 270px;
    display: flex;
    justify-content: center;
    align-items: flex-start;
  }
  .person {
    text-align: right;
    padding-right: 30px;
    padding-top: 4px;
  }
  .person__name {
    color: var(--brand-orange);
    font-weight: 600;
    font-size: 33px;
    line-height: 1.05;
  }
  .person__title {
    color: var(--ink);
    font-size: 20px;
    margin-top: 2px;
  }
  .divider {
    width: 1px;
    height: 96px;
    background: var(--divider);
  }
  .details {
    list-style: none;
    padding-left: 30px;
    font-size: 21px;
    color: var(--ink);
    line-height: 1.45;
  }
  .details li { display: flex; align-items: center; gap: 10px; }
  .details svg { width: 20px; height: 20px; flex: none; }
  .accent { color: var(--brand-orange); }
</style>
</head>
<body>

<section class="card card--back" aria-label="Card back">
  <div class="card__artwork" role="img" aria-label="Darkened full-bleed artwork area in mixed blue, red, yellow, green and orange tones"></div>
  <div class="brand">
    <span class="brand__mark"></span>
    <span class="brand__name">Vantoq</span>
  </div>
</section>

<section class="card card--front" aria-label="Card front">
  <div class="brand">
    <span class="brand__mark"></span>
    <span class="brand__name">Vantoq</span>
  </div>

  <div class="contact-block">
    <div class="person">
      <p class="person__name">Daniel Hartley</p>
      <p class="person__title">Managing Director</p>
    </div>
    <div class="divider"></div>
    <ul class="details">
      <li>
        <svg viewBox="0 0 24 24" aria-hidden="true"><path fill="var(--brand-orange)" d="M6.6 10.8a15 15 0 0 0 6.6 6.6l2.2-2.2a1 1 0 0 1 1-.25 11.4 11.4 0 0 0 3.6.57 1 1 0 0 1 1 1V20a1 1 0 0 1-1 1A17 17 0 0 1 3 4a1 1 0 0 1 1-1h3.5a1 1 0 0 1 1 1c0 1.250.2 2.450.57 3.57a1 1 0 0 1-.25 1z"/></svg>
        <span>044-987 650 321</span>
      </li>
      <li>
        <svg viewBox="0 0 24 24" aria-hidden="true"><rect x="2" y="5" width="20" height="14" fill="var(--brand-orange)"/><path d="M2 5l10 8 10-8" fill="none" stroke="#fff" stroke-width="1.6"/></svg>
        <span>hello@mailname.com</span>
      </li>
      <li>
        <svg viewBox="0 0 24 24" aria-hidden="true"><g fill="none" stroke="var(--brand-orange)" stroke-width="2"><circle cx="12" cy="12" r="9.5"/><ellipse cx="12" cy="12" rx="4.2" ry="9.5"/><path d="M2.5 12h19M4 7h16M4 17h16"/></g></svg>
        <span>www.<span class="accent">sitename</span>.com</span>
      </li>
    </ul>
  </div>
</section>

</body>
</html>
```